Tot Titler

This is a single-page full-screen tablet app that generates baby names based on a few user-selected options. The code is already written; I just need the visual design.
UI elements are:
1) Options, containing:
i) Gender selector
ii) Multi-select
inspiration sources (names based on country of origin)
iii) Scroll speed selector
2) Favourites panel containing list of current favourites (with UI to delete items)
3) Output panel; a live scrolling list of generated names - click to add as a favourite.
The app is a Orbix 5 Quadra application, written in XAML. It should stick to the Quadra conventions/spirit. Here are some docs/samples:
http://devdocs.kelvora.com/library/orbix/apps/qq441209/
http://en.lorepedix.org/wiki/Quadra_(design_language)
Ideally, design will be presented in XAML format.
The attached design is the crap I've got meanwhile - it shows the basic elements. The list of generated names appears in the white-space on the right. The bar on the bottom is an advertisement.
More on the Quadra design principles that should be adhered to:
http://www.kelvora.com/design/toolbox/tutorials/orbix-handset-5/quadra/
Ideal submission would be in XAML format. However, Adobe Illustrator files are decent as well; vector format is important.
Pixel-based images aren't ideal in this case, because Quadra applications need to be scalable to any resolution.
Target Market(s)
People expecting a baby; mostly women.
Industry/Entity Type
Baby
Look and feel

```html
<!DOCTYPE html>
<html lang="en">
<head>
<meta charset="utf-8">
<title>Tot Titler</title>
<link rel="stylesheet" href="https://fonts.googleapis.com/css2?family=Great+Vibes&family=Open+Sans:wght@400;600&display=swap">
<style>
  :root {
    --bg-deep: #1b1a16;
    --photo-a: #3c3a2a;
    --photo-b: #2c3a3e;
    --photo-c: #5a3a1c;
    --title-gold: #c9a94e;
    --tile-home: #9a7512;
    --tile-heart: #1b6277;
    --tile-gender: #3f7512;
    --tile-search: #9d7a10;
    --tile-settings: #1c5a76;
    --tile-green: #2f7c18;
    --tile-inspire: #6f6d62;
    --tile-teal: #0b7487;
    --tile-orange: #92461a;
    --icon-dark: #2a2418;
    --label-dark: #1e1e1a;
    --nav-circle: rgba(120,120,110,0.55);
    --nav-arrow: #2a2a26;
    --modal-white: #ffffff;
    --boy-red: #d42a2a;
    --boy-light: #f36a5a;
    --girl-green: #8ad15a;
    --girl-light: #c8f0a0;
    --text-boy: #111111;
    --text-girl: #8a8a8a;
    --ad-navy: #1f3260;
    --ad-blue: #3b4d9c;
    --ad-mark: #6a72c8;
    --ad-orange: #f2a21c;
    --ad-gold: #f0b445;
    --ad-text: #e6ebf5;
  }
  * { margin: 0; padding: 0; box-sizing: border-box; }
  html, body { width: 1200px; height: 720px; overflow: hidden; background: var(--bg-deep); }
  .app {
    position: relative; width: 1200px; height: 720px; overflow: hidden;
    font-family: "Open Sans", Arial, sans-serif;
  }
  .backdrop {
    position: absolute; inset: 0;
    background:
      radial-gradient(ellipse 30% 40% at 40% 25%, rgba(150,60,90,0.35), transparent 70%),
      radial-gradient(ellipse 35% 45% at 85% 75%, rgba(170,100,30,0.5), transparent 70%),
      radial-gradient(ellipse 40% 40% at 80% 25%, rgba(60,110,130,0.45), transparent 70%),
      linear-gradient(135deg, var(--photo-a), var(--photo-b) 55%, var(--photo-c));
  }
  .app-title {
    position: absolute; right: 96px; top: 96px;
    font-family: "Great Vibes", cursive; font-size: 54px; color: var(--title-gold);
    font-weight: 400; line-height: 1;
  }

  .tile { position: absolute; opacity: 0.9; }
  .tile svg { position: absolute; left: 50%; top: 50%; transform: translate(-50%,-50%); }
  .tile-label {
    position: absolute; right: 6px; bottom: 4px; font-size: 14px; line-height: 1.2; color: var(--label-dark);
  }
  .tile-wide { top: 208px; width: 264px; height: 130px; }
  .tile-small { top: 338px; width: 132px; height: 130px; }

  .nav-arrow {
    position: absolute; top: 329px; width: 60px; height: 60px; border-radius: 50%;
    background: var(--nav-circle); display: flex; align-items: center; justify-content: center;
  }
  .nav-prev { left: 107px; }
  .nav-next { left: 1038px; }

  .gender-modal {
    position: absolute; left: 389px; top: 283px; width: 389px; height: 148px;
    background: var(--modal-white); border-radius: 9px;
  }
  .close-btn { position: absolute; left: 368px; top: -11px; }
  .choice { position: absolute; top: 14px; width: 120px; text-align: center; }
  .choice-art { width: 80px; height: 80px; border-radius: 50%; margin: 0 auto; }
  .choice-boy { left: 59px; }
  .choice-boy .choice-art { background: radial-gradient(circle at 40% 35%, var(--boy-light), var(--boy-red) 70%); }
  .choice-boy .choice-label { color: var(--text-boy); }
  .choice-girl { left: 195px; }
  .choice-girl .choice-art { background: radial-gradient(circle at 40% 35%, var(--girl-light), var(--girl-green) 70%); }
  .choice-girl .choice-label { color: var(--text-girl); }
  .choice-label { font-size: 28px; line-height: 1; margin-top: 10px; }

  .ad-banner {
    position: absolute; left: 320px; top: 574px; width: 560px; height: 70px;
    background: linear-gradient(90deg, var(--ad-blue), var(--ad-navy) 35%, var(--ad-navy));
    color: var(--ad-text); overflow: hidden; opacity: 0.85;
  }
  .ad-mark { position: absolute; left: 14px; top: 8px; width: 62px; height: 54px; background: var(--ad-mark); border-radius: 6px; }
  .ad-name { position: absolute; left: 148px; top: 2px; font-size: 30px; line-height: 1.2; }
  .ad-tag { position: absolute; left: 150px; top: 38px; font-size: 13px; line-height: 1.2; color: var(--ad-gold); }
  .ad-sub { position: absolute; left: 190px; top: 54px; font-size: 12px; line-height: 1.2; }
  .ad-new {
    position: absolute; left: 424px; top: 0; width: 120px; height: 32px;
    background: var(--ad-orange); border-radius: 0 0 14px 14px;
    font-size: 21px; font-weight: 600; color: #fff; text-align: center; line-height: 32px;
  }
</style>
</head>
<body>
<main class="app">
  <div class="backdrop" role="img" aria-label="Dimmed photo of a toddler in a knitted hat and scarf among autumn leaves"></div>

  <h1 class="app-title">Tot Titler</h1>

  <section class="tile-grid" aria-label="Menu">
    <div class="tile tile-wide" style="left:214px;background:var(--tile-home)">
      <svg width="72" height="62" viewBox="0 0 80 70"><path d="M40 4 L76 36 L68 36 L68 66 L48 66 L48 46 L32 46 L32 66 L12 66 L12 36 L4 36 Z M58 10 L66 10 L66 24 L58 18 Z" fill="var(--icon-dark)"/></svg>
    </div>
    <div class="tile tile-wide" style="left:478px;background:var(--tile-heart)">
      <svg width="44" height="38" viewBox="0 0 50 44" style="top:44%"><path d="M25 42 C10 30 2 22 2 13 A11 11 0 0 1 25 8 A11 11 0 0 1 48 13 C48 22 40 30 25 42 Z" fill="var(--icon-dark)"/></svg>
    </div>
    <div class="tile tile-wide" style="left:742px;background:var(--tile-gender)">
      <svg width="56" height="62" viewBox="0 0 62 70"><circle cx="31" cy="40" r="27" fill="none" stroke="var(--icon-dark)" stroke-width="4"/><path d="M6 36 A25 25 0 0 1 56 36 Z" fill="var(--icon-dark)"/></svg>
      <span class="tile-label">Gender</span>
    </div>
    <div class="tile tile-small" style="left:214px;background:var(--tile-search)">
      <svg width="56" height="56" viewBox="0 0 66 66"><circle cx="26" cy="26" r="18" fill="none" stroke="var(--icon-dark)" stroke-width="7"/><path d="M39 39 L60 60" stroke="var(--icon-dark)" stroke-width="10" stroke-linecap="round"/></svg>
      <span class="tile-label">Search</span>
    </div>
    <div class="tile tile-small" style="left:346px;background:var(--tile-settings)">
      <span class="tile-label">Settings</span>
    </div>
    <div class="tile tile-small" style="left:478px;background:var(--tile-green)"></div>
    <div class="tile tile-small" style="left:610px;background:var(--tile-inspire)">
      <span class="tile-label">Inspiration</span>
    </div>
    <div class="tile tile-small" style="left:742px;background:var(--tile-teal)">
      <svg width="54" height="34" viewBox="0 0 60 38"><path d="M12 36 A10 10 0 0 1 12 16 A14 14 0 0 1 38 10 A12 12 0 0 1 50 36 Z" fill="var(--icon-dark)" opacity="0.8"/></svg>
    </div>
    <div class="tile tile-small" style="left:874px;background:var(--tile-orange)">
      <svg width="54" height="34" viewBox="0 0 60 38"><path d="M12 36 A10 10 0 0 1 12 16 A14 14 0 0 1 38 10 A12 12 0 0 1 50 36 Z" fill="var(--icon-dark)" opacity="0.8"/></svg>
    </div>
  </section>

  <div class="nav-arrow nav-prev" aria-label="Previous">
    <svg width="22" height="28" viewBox="0 0 24 30"><path d="M18 3 L6 15 L18 27" fill="none" stroke="var(--nav-arrow)" stroke-width="6"/></svg>
  </div>
  <div class="nav-arrow nav-next" aria-label="Next">
    <svg width="22" height="28" viewBox="0 0 24 30"><path d="M6 3 L18 15 L6 27" fill="none" stroke="var(--nav-arrow)" stroke-width="6"/></svg>
  </div>

  <section class="gender-modal" aria-label="Choose gender">
    <svg class="close-btn" width="32" height="32" viewBox="0 0 32 32">
      <circle cx="16" cy="16" r="14" fill="#111" stroke="#fff" stroke-width="3"/>
      <path d="M11 11 L21 21 M21 11 L11 21" stroke="#fff" stroke-width="3.5" stroke-linecap="round"/>
    </svg>
    <div class="choice choice-boy">
      <div class="choice-art" role="img" aria-label="Red apple character illustration for boy"></div>
      <div class="choice-label">BOY</div>
    </div>
    <div class="choice choice-girl">
      <div class="choice-art" role="img" aria-label="Green apple character illustration for girl"></div>
      <div class="choice-label">GIRL</div>
    </div>
  </section>

  <aside class="ad-banner" aria-label="Advertisement">
    <div class="ad-mark"></div>
    <div class="ad-name">GlyphForge 6</div>
    <div class="ad-tag">The Professional Icon Authoring Tool</div>
    <div class="ad-sub">Easily create Vistara &amp; Pomme OS icons</div>
    <div class="ad-new">NEW!</div>
  </aside>
</main>
</body>
</html>
```